Coastline Premier Retreats Business Card Design

Design a business card for Coastline Premier Retreats. Look at the website for colors and reference. Card should have logo, name, title, office number, mobile number, email, URL and a tagline like, "Luxury Hotel & Resort Email Marketing" (This might change).

https://www.coastlinepremierretreats.example

The rest I will leave up to your imagination.

Contact Information for Business Card

Logo, name, title, office number, mobile number, email, URL and a tagline like, "Luxury Hotel & Resort Email Marketing" (This might change).

```html
<!DOCTYPE html>
<html lang="en">
<head>
<meta charset="utf-8">
<title>Coastline Premier Retreats – Business Card</title>
<link href="https://fonts.googleapis.com/css2?family=Arimo:wght@400;700&display=swap" rel="stylesheet">
<style>
  :root {
    --orange: #f37321;
    --ink: #1a1a1a;
    --paper: #ffffff;
    --backdrop-top: #e9e9e9;
    --backdrop-bottom: #cfcfcf;
  }
  * { box-sizing: border-box; margin: 0; padding: 0; }
  html, body { width: 1200px; height: 856px; overflow: hidden; }
  body {
    background: linear-gradient(180deg, var(--backdrop-top), var(--backdrop-bottom));
    font-family: "Arimo", Arial, sans-serif;
    position: relative;
  }
  .card {
    position: absolute;
    width: 540px;
    height: 309px;
    overflow: hidden;
    box-shadow: 0 10px 28px rgba(0,0,0,0.28);
  }
  .card-front { left: 40px; top: 130px; background: var(--paper); }
  .card-back  { left: 620px; top: 417px; background: var(--orange); }

  .front-wave { position: absolute; inset: 0; width: 100%; height: 100%; }

  .brand {
    position: absolute;
    display: flex;
    align-items: center;
    gap: 10px;
    font-weight: 700;
    text-transform: uppercase;
    letter-spacing: 0.5px;
  }
  .brand-mark { flex: none; }
  .card-front .brand { left: 30px; top: 112px; width: 200px; color: var(--ink); font-size: 18px; line-height: 1.15; }
  .card-front .brand-mark { width: 14px; height: 14px; background: var(--orange); }
  .card-back .brand { left: 0; right: 0; top: 0; bottom: 0; justify-content: center; color: var(--paper); font-size: 30px; line-height: 1.15; }
  .card-back .brand-mark { width: 22px; height: 22px; background: var(--paper); }

  .divider {
    position: absolute;
    left: 245px; top: 40px;
    width: 1.5px; height: 150px;
    background: var(--orange);
  }
  .details { position: absolute; left: 262px; top: 30px; color: var(--ink); }
  .person-name { color: var(--orange); font-weight: 700; font-size: 18px; letter-spacing: 0.5px; text-transform: uppercase; line-height: 22px; }
  .person-title, .tagline { font-size: 13px; line-height: 16px; }
  .contact-list { list-style: none; margin-top: 6px; }
  .contact-list li { display: flex; align-items: center; gap: 6px; font-size: 11.5px; line-height: 16px; }
  .contact-list svg { width: 12px; height: 12px; flex: none; }
</style>
</head>
<body>

<section class="card card-front" aria-label="Business card front">
  <svg class="front-wave" viewBox="0 0 540 309" preserveAspectRatio="none" aria-hidden="true">
    <path d="M0 282 C150 277 240 257 320 232 S460 204 540 197 L540 309 L0 309 Z" fill="var(--ink)"/>
    <path d="M0 286 C150 281 240 261 320 236 S460 208 540 201 L540 309 L0 309 Z" fill="var(--paper)"/>
    <path d="M0 290 C150 285 240 265 320 240 S460 212 540 205 L540 309 L0 309 Z" fill="var(--orange)"/>
  </svg>

  <div class="brand">
    <span class="brand-mark"></span>
    <span class="brand-name">Coastline Premier Retreats</span>
  </div>

  <div class="divider"></div>

  <div class="details">
    <p class="person-name">Daniel Whitcombe</p>
    <p class="person-title">Co-Founder</p>
    <p class="tagline">Luxury Hotel &amp; Resort<br>Email Marketing</p>
    <ul class="contact-list">
      <li>
        <svg viewBox="0 0 12 12" aria-hidden="true"><path d="M1 4 C1 2 3 1 6 1 S11 2 11 4 L8.5 4.5 L8 3 H4 L3.5 4.5 Z M3 6 H9 L10 11 H2 Z" fill="var(--orange)"/></svg>
        843-555-0147
      </li>
      <li>
        <svg viewBox="0 0 12 12" aria-hidden="true"><rect x="3" y="0.8" width="6" height="10.4" rx="1.2" fill="none" stroke="var(--orange)" stroke-width="1.2"/><circle cx="6" cy="9.4" r="0.7" fill="var(--orange)"/></svg>
        874-555-0193
      </li>
      <li>
        <svg viewBox="0 0 12 12" aria-hidden="true"><rect x="0.8" y="2.5" width="10.4" height="7" fill="var(--orange)"/><path d="M1 3 L6 7 L11 3" fill="none" stroke="var(--paper)" stroke-width="0.9"/></svg>
        info@coastlinepremierretreats.example
      </li>
      <li>
        <svg viewBox="0 0 12 12" aria-hidden="true"><circle cx="6" cy="6" r="5.2" fill="var(--orange)"/><path d="M1 6 H11 M6 0.8 C3.5 3.5 3.5 8.5 6 11.2 M6 0.8 C8.5 3.5 8.5 8.5 6 11.2" fill="none" stroke="var(--paper)" stroke-width="0.7"/></svg>
        www.coastlinepremierretreats.example
      </li>
    </ul>
  </div>
</section>

<section class="card card-back" aria-label="Business card back">
  <div class="brand">
    <span class="brand-mark"></span>
    <span class="brand-name">Coastline Premier Retreats</span>
  </div>
</section>

</body>
</html>
```